Small Business Broker Business Card Design

A business card design for a small business brokerage, which is a financial service, not unlike real estate brokerage, but for small businesses such as laundromats, pizza shops, restaurants, cleaners etc. The designs should all be simple, more conservative in nature, using the colors and font of the logo. Again, think real estate Brokerage as a business context
Contact Information for Business Card
Name: Glen R. Harlow. Title: Small Business Advisor. Email: g.harlow@bayfieldcapitalworks.example. Mobile: (555) 274-3918. Office: (555) 806-2147. www.bayfieldcapitalworks.example

```html
<!DOCTYPE html>
<html lang="en">
<head>
<meta charset="utf-8">
<title>Bayfield Capital Works – Business Card</title>
<link rel="stylesheet" href="https://fonts.googleapis.com/css2?family=Montserrat:wght@400;500;600;700;800&display=swap">
<style>
  :root {
    --navy: #1d3a6e;
    --green: #8cc63f;
    --white: #ffffff;
    --backdrop: #e6e8eb;
    --ink-soft: #24406f;
  }
  * { box-sizing: border-box; margin: 0; padding: 0; }
  html, body {
    width: 1200px; height: 900px; overflow: hidden;
    background: var(--backdrop);
    font-family: "Montserrat", Arial, sans-serif;
  }
  .sheet {
    width: 1200px; height: 900px;
    display: flex; flex-direction: column; align-items: center;
    justify-content: center; gap: 20px;
  }
  .card {
    position: relative;
    width: 700px; height: 400px;
    border-radius: 22px;
    overflow: hidden;
  }

  /* Front */
  .card--front {
    background: var(--green);
    display: flex; flex-direction: column; align-items: center; justify-content: center;
    padding: 0 48px;
  }
  .wordmark {
    display: flex; align-items: center; gap: 14px;
  }
  .wordmark__square {
    width: 26px; height: 26px; background: var(--navy); flex: none;
  }
  .wordmark__name {
    color: var(--navy); font-weight: 800; font-size: 30px;
    letter-spacing: 0.5px; text-transform: uppercase; line-height: 1;
    white-space: nowrap;
  }
  .tagline {
    margin-top: 12px; color: var(--white); font-weight: 600; font-size: 13px;
    letter-spacing: 2px; text-transform: uppercase; white-space: nowrap;
  }

  /* Back */
  .card--back { background: var(--white); }
  .identity {
    position: absolute; left: 48px; top: 48px;
  }
  .identity__name {
    color: var(--navy); font-weight: 800; font-size: 30px; line-height: 1.1;
  }
  .identity__title {
    color: var(--ink-soft); font-weight: 500; font-size: 16px; margin-top: 4px;
  }
  .rule {
    position: absolute; left: 48px; right: 48px; top: 132px;
    height: 1.5px; background: var(--green);
  }
  .contacts {
    position: absolute; left: 48px; top: 152px;
    list-style: none;
  }
  .contacts li {
    display: flex; align-items: center; gap: 12px;
    color: var(--navy); font-size: 15px; font-weight: 500; line-height: 26px;
  }
  .contacts svg { width: 15px; height: 15px; fill: var(--navy); flex: none; }
  .back-brand {
    position: absolute; right: 48px; bottom: 42px; text-align: right;
  }
  .back-brand .tagline { color: var(--green); margin-top: 10px; font-weight: 700; }
  .band {
    position: absolute; left: 0; right: 0; bottom: 0; height: 18px; background: var(--green);
  }
</style>
</head>
<body>
<main class="sheet">
  <section class="card card--front" aria-label="Card front">
    <div class="wordmark">
      <span class="wordmark__square"></span>
      <span class="wordmark__name">Bayfield Capital Works, Inc</span>
    </div>
    <p class="tagline">Trusted guidance for every neighborhood business</p>
  </section>

  <section class="card card--back" aria-label="Card back">
    <div class="identity">
      <h1 class="identity__name">Glen R. Harlow</h1>
      <p class="identity__title">Small Business Advisor</p>
    </div>
    <div class="rule"></div>
    <ul class="contacts">
      <li>
        <svg viewBox="0 0 16 16" aria-hidden="true"><path d="M2 5c0-2 3-3 6-3s6 1 6 3v1h-3V5H5v1H2z"/><path d="M4 7h8l2 7H2z"/></svg>
        (555) 806-2147
      </li>
      <li>
        <svg viewBox="0 0 16 16" aria-hidden="true"><path d="M4 1h3l1 4-2 1c1 2 2 3 4 4l1-2 4 1v3c0 1-1 2-2 2C7 14 2 9 2 3c0-1 1-2 2-2z"/></svg>
        (555) 274-3918
      </li>
      <li>
        <svg viewBox="0 0 16 16" aria-hidden="true"><path d="M1 3h14v1L8 9 1 4z"/><path d="M1 6l7 5 7-5v7H1z"/></svg>
        g.harlow@bayfieldcapitalworks.example
      </li>
      <li>
        <svg viewBox="0 0 16 16" aria-hidden="true"><path d="M8 1a7 7 0 1 0 0 14A7 7 0 0 0 8 1zm0 1.5c.9 0 1.9 1.7 2.2 4.5H5.8C6.1 4.2 7.1 2.5 8 2.5zM2.6 7h1.8c.1-1.6.4-3 1-4A5.6 5.6 0 0 0 2.6 7zm0 2a5.6 5.6 0 0 0 2.8 4c-.6-1-.9-2.4-1-4zm3.2 0h4.4c-.3 2.8-1.3 4.5-2.2 4.5S6.1 11.8 5.8 9zm5.8 0c-.1 1.6-.4 3-1 4a5.6 5.6 0 0 0 2.8-4zm1.8-2a5.6 5.6 0 0 0-2.8-4c.6 1 .9 2.4 1 4z"/></svg>
        www.bayfieldcapitalworks.example
      </li>
    </ul>
    <div class="back-brand">
      <span class="wordmark__name">Bayfield Capital Works, Inc</span>
      <p class="tagline">Trusted guidance for every neighborhood business</p>
    </div>
    <div class="band"></div>
  </section>
</main>
</body>
</html>
```